Local fast-growing company in the service sector

We are looking for a modern business card design, which should also appear on our letterheads

Target Market(s)

Private and industrial sectors

Contact Information for Business Card

Vorname Name
Kellberger Str. 18
70999 Kellbach
Tel.: 07146-839214-0
Name@agentur-kvtl.de

Colors
9d9d9d
919191
aaaaaa

Requirements
Must have
• The logo (file) in silver

```html
<!DOCTYPE html>
<html lang="de">
<head>
<meta charset="utf-8">
<title>KVTL Visitenkarte</title>
<link rel="stylesheet" href="https://fonts.googleapis.com/css2?family=Arimo:wght@400;700&display=swap">
<style>
  :root {
    --page: #2b2b2b;
    --card-top: #ffffff;
    --card-bottom: #e4e4e4;
    --silver: #9d9d9d;
    --silver-mid: #919191;
    --silver-light: #aaaaaa;
    --ink: #1f2430;
    --ink-soft: #3a3f4a;
    --tab: #1c1c1c;
  }
  * { margin: 0; padding: 0; box-sizing: border-box; }
  html, body { width: 1200px; height: 997px; overflow: hidden; }
  body {
    background: var(--page);
    font-family: "Arimo", Arial, sans-serif;
    position: relative;
  }
  .card {
    position: absolute;
    left: 180px; top: 258px;
    width: 840px; height: 480px;
    background: linear-gradient(160deg, var(--card-top) 0%, #f3f3f3 55%, var(--card-bottom) 100%);
    overflow: hidden;
  }
  .brand {
    position: absolute; left: 250px; top: 92px;
    display: flex; align-items: center; gap: 22px;
  }
  .brand-square {
    width: 86px; height: 86px;
    background: var(--silver);
  }
  .brand-text { display: flex; flex-direction: column; }
  .brand-name {
    font-size: 84px; font-weight: 700; line-height: 0.9;
    color: var(--silver-mid); letter-spacing: 2px;
  }
  .brand-web {
    font-size: 28px; font-weight: 700; color: var(--silver-mid);
    letter-spacing: 1px; margin-top: 4px;
  }
  .holder {
    position: absolute; right: 40px; top: 232px; text-align: right;
  }
  .holder-name {
    font-size: 24px; font-weight: 700; color: var(--silver-mid);
    letter-spacing: 1px; text-transform: uppercase;
  }
  .holder-role {
    font-size: 19px; font-weight: 700; color: var(--ink);
    text-transform: uppercase;
  }
  .edge-tab {
    position: absolute; right: 0; top: 222px;
    width: 16px; height: 70px;
    background: var(--tab); border-radius: 8px 0 0 8px;
  }
  .icon-strip {
    position: absolute; left: 0; top: 330px;
    width: 44px; height: 150px;
    background: var(--silver-light);
    border-radius: 0 10px 0 0;
    display: flex; flex-direction: column; align-items: center;
    justify-content: space-around; padding: 10px 0;
  }
  .icon-strip svg { width: 22px; height: 22px; fill: #ffffff; }
  .contact {
    position: absolute; left: 70px; top: 342px;
    list-style: none;
  }
  .contact li {
    font-size: 24px; line-height: 32px; color: var(--ink-soft);
    letter-spacing: 0.5px;
  }
  .bottom-band {
    position: absolute; left: 0; bottom: 0; width: 100%; height: 150px;
  }
</style>
</head>
<body>
  <main class="card" aria-label="Visitenkarte KVTL">
    <svg class="bottom-band" viewBox="0 0 840 150" preserveAspectRatio="none" aria-hidden="true">
      <path d="M520 150 L520 40 Q520 10 560 10 L840 10 L840 150 Z" fill="#c9c9c9"/>
      <path d="M540 150 L540 50 Q540 26 575 26 L840 26 L840 150 Z" fill="#b4b4b4"/>
      <rect x="0" y="140" width="840" height="10" fill="#9d9d9d"/>
    </svg>

    <div class="brand">
      <div class="brand-square"></div>
      <div class="brand-text">
        <span class="brand-name">KVTL</span>
        <span class="brand-web">agentur-kvtl.de</span>
      </div>
    </div>

    <div class="edge-tab"></div>
    <div class="holder">
      <p class="holder-name">Jonas B. Keller</p>
      <p class="holder-role">President &amp; CEO</p>
    </div>

    <div class="icon-strip" aria-hidden="true">
      <svg viewBox="0 0 24 24"><path d="M6.6 10.8a15 15 0 0 0 6.6 6.6l2.2-2.2c.3-.3.7-.4 1-.2 1.1.4 2.3.6 3.6.6.6 0 1 .4 1 1V20c0 .6-.4 1-1 1A17 17 0 0 1 3 4c0-.6.4-1 1-1h3.5c.6 0 1 .4 1 1 0 1.3.2 2.5.6 3.6.1.3 0 .7-.2 1z"/></svg>
      <svg viewBox="0 0 24 24"><path d="M6 3h12v5H6zM4 9h16a2 2 0 0 1 2 2v6h-4v4H6v-4H2v-6a2 2 0 0 1 2-2zm4 7v3h8v-3z"/></svg>
      <svg viewBox="0 0 24 24"><path d="M2 5h20v14H2zm2 2v.5l8 5 8-5V7l-8 5z"/></svg>
      <svg viewBox="0 0 24 24"><path d="M12 2a7 7 0 0 0-7 7c0 5 7 13 7 13s7-8 7-13a7 7 0 0 0-7-7zm0 9.5A2.5 2.5 0 1 1 12 6.5a2.5 2.5 0 0 1 0 5z"/></svg>
    </div>

    <ul class="contact">
      <li>+49 (7146) 8392140</li>
      <li>+49 (7146) 8392149</li>
      <li>Name@agentur-kvtl.de</li>
      <li>Kellberger Str. 18, 70999 Kellbach</li>
    </ul>
  </main>
</body>
</html>
```